Business Card for Industrial Distributor

We need a business card design for an industrial distributor. We sell machine parts for the manufacturing and oil industry. We would like the cards to look clean and modern but with a touch of industry.

Our colors are blue/white.

Please feel free to visit our website www.korvelpartsco.com

Target Market(s)

mexican manufacturers in the automobile/aerospace industry

Industry/Entity Type

Industrial

Colors
ffffff
0555a3

```html
<!DOCTYPE html>
<html lang="en">
<head>
<meta charset="utf-8">
<title>Korvel Business Card</title>
<link rel="stylesheet" href="https://fonts.googleapis.com/css2?family=Source+Sans+3:wght@400;600;700&display=swap">
<style>
  :root {
    --stage: #c6c6c6;
    --card-white: #ffffff;
    --brand-blue: #1f3296;
    --brand-blue-deep: #1b3aa6;
    --brand-blue-light: #2f5cc8;
    --ink: #2b2b2b;
    --rule: #cfcfcf;
  }
  * { box-sizing: border-box; margin: 0; padding: 0; }
  html, body { width: 1200px; height: 900px; overflow: hidden; }
  body {
    background: var(--stage);
    font-family: "Source Sans 3", "Myriad Pro", sans-serif;
    position: relative;
  }
  .card {
    position: absolute;
    top: 306px;
    width: 440px;
    height: 271px;
    border-radius: 12px;
    overflow: hidden;
  }
  .card-front { left: 149px; background: var(--card-white); }
  .card-back { left: 608px; }

  .brand-mark {
    position: absolute;
    border-radius: 50%;
  }
  .card-front .brand-mark {
    left: 53px; top: 59px; width: 106px; height: 106px;
    background: var(--brand-blue-deep);
  }
  .brand-name {
    position: absolute;
    font-weight: 700;
    white-space: nowrap;
    line-height: 1;
  }
  .card-front .brand-name {
    left: 21px; top: 174px; width: 170px; text-align: center;
    font-size: 38px; color: var(--brand-blue);
  }
  .divider {
    position: absolute; left: 217px; top: 62px;
    width: 1px; height: 152px; background: var(--rule);
  }
  .contact-block { position: absolute; left: 229px; top: 56px; color: var(--ink); }
  .person-name {
    font-size: 15.5px; font-weight: 600; color: var(--brand-blue);
    letter-spacing: 0.2px; line-height: 18px;
  }
  .person-title { font-size: 13px; line-height: 16px; margin-left: 1px; }
  .contact-list { list-style: none; margin-top: 14px; }
  .contact-list li {
    font-size: 12.8px; line-height: 16px; display: flex; align-items: center;
  }
  .contact-list svg { width: 9px; height: 9px; margin: 0 6px 0 2px; fill: var(--brand-blue); }
  .address { margin-top: 13px; font-size: 12.8px; line-height: 16.5px; margin-left: 2px; }

  .back-pattern {
    position: absolute; inset: 0;
    background: radial-gradient(ellipse at 50% 50%, var(--brand-blue-light) 0%, var(--brand-blue-deep) 75%);
  }
  .card-back .brand-mark {
    left: 57px; top: 99px; width: 70px; height: 70px; background: var(--card-white);
  }
  .card-back .brand-name {
    left: 136px; top: 108px; font-size: 54px; color: var(--card-white);
  }
</style>
</head>
<body>
  <section class="card card-front">
    <div class="brand-mark"></div>
    <div class="brand-name">Korvel</div>
    <div class="divider"></div>
    <div class="contact-block">
      <p class="person-name">DANIEL REYES</p>
      <p class="person-title">Managing Director</p>
      <ul class="contact-list">
        <li><svg viewBox="0 0 10 10"><path d="M1 3.5C1 2 2.5 1 5 1s4 1 4 2.5L7.5 4 7 3H3l-.5 1zM2.5 5h5L8.5 9h-7z"/></svg>(044) 123 456 789</li>
        <li><svg viewBox="0 0 10 10"><path d="M3 0h4a1 1 0 0 1 1 1v8a1 1 0 0 1-1 1H3a1 1 0 0 1-1-1V1a1 1 0 0 1 1-1zm.5 1.5v6h3v-6z"/></svg>(044)123456789</li>
        <li><svg viewBox="0 0 10 10"><path d="M0 2h10v6H0zM1 2.8l4 3 4-3v-.1l-4 2.6-4-2.6z"/></svg>info@youremail.com</li>
        <li><svg viewBox="0 0 10 10"><circle cx="5" cy="5" r="4.5"/></svg>www.korvelpartsco.com</li>
      </ul>
      <p class="address">12345,your address goes here,<br>country name,12345</p>
    </div>
  </section>

  <section class="card card-back">
    <div class="back-pattern" role="img" aria-label="Blue background with a repeating pattern of small raised dots"></div>
    <div class="brand-mark"></div>
    <div class="brand-name">Korvel</div>
  </section>
</body>
</html>
```